design a construction company business card

Design business card around our logo. Card must have all the typical info: name, title, address, phone, email, business name, etc. Somewhere on the card I would like to see our motto "Built on integrity... Inspired by commitment." Consider adding a splash of bright orange to the card to complement the blues and silvers/grays in the logo. We are open to metallic inks, textures, etc. We would like to see options on both light and dark backgrounds. The font in the logo is Euro Technic Extended Regular.

```html
<!DOCTYPE html>
<html lang="en">
<head>
<meta charset="utf-8">
<title>Halden Contracting – Business Card</title>
<link rel="stylesheet" href="https://fonts.googleapis.com/css2?family=Open+Sans:wght@400;600;700&display=swap">
<style>
  :root {
    --stage-light: #eceded;
    --stage-dark: #c9cacb;
    --card-white: #ffffff;
    --brand-blue: #2a7fd6;
    --brand-blue-deep: #1d5fb4;
    --brand-navy: #1f4f8f;
    --swoosh-gray: #9a9ea3;
    --text-light: #ffffff;
    --text-muted: #6b7079;
  }
  * { box-sizing: border-box; margin: 0; padding: 0; }
  html, body { width: 800px; height: 1200px; overflow: hidden; }
  body {
    font-family: "Open Sans", Arial, sans-serif;
    background: radial-gradient(ellipse at 50% 45%, var(--stage-light) 0%, var(--stage-dark) 100%);
    position: relative;
  }
  .card {
    position: absolute;
    overflow: hidden;
    box-shadow: 0 4px 10px rgba(0,0,0,0.25);
  }
  .card--front {
    left: 147px; top: 165px; width: 506px; height: 368px;
    background: var(--card-white);
  }
  .card--back {
    left: 115px; top: 701px; width: 570px; height: 291px;
    background: var(--brand-blue);
  }
  .card__wave { position: absolute; inset: 0; }
  .wordmark {
    position: absolute;
    display: flex; flex-direction: column; align-items: center;
    font-weight: 700; letter-spacing: 3px;
  }
  .wordmark__row { display: flex; align-items: center; gap: 8px; }
  .wordmark__mark { width: 14px; height: 14px; }
  .wordmark__name { font-size: 30px; line-height: 1; }
  .wordmark__sub { font-size: 11px; letter-spacing: 2px; margin-top: 4px; font-weight: 700; }
  .card--front .wordmark { left: 24px; top: 66px; color: var(--brand-navy); }
  .card--front .wordmark__mark { background: var(--brand-blue); }
  .card--back .wordmark { left: 0; right: 0; top: 118px; color: var(--text-light); }
  .card--back .wordmark__mark { background: var(--text-light); }
  .holder { position: absolute; left: 20px; top: 136px; }
  .holder__name { font-size: 19px; font-weight: 700; color: var(--brand-blue-deep); line-height: 1.2; }
  .holder__title { font-size: 11px; color: var(--text-muted); margin-top: 1px; }
  .contact {
    position: absolute; right: 30px; top: 120px;
    text-align: right; color: var(--text-light);
    font-size: 11px; line-height: 16px;
  }
  .contact__address { margin-bottom: 44px; }
  .contact__line { display: flex; justify-content: flex-end; align-items: center; gap: 8px; }
  .contact__icon { width: 10px; height: 10px; fill: var(--text-light); }
</style>
</head>
<body>

<section class="card card--front">
  <svg class="card__wave" viewBox="0 0 506 368" preserveAspectRatio="none" aria-hidden="true">
    <defs>
      <linearGradient id="blueFill" x1="0" y1="1" x2="1" y2="0">
        <stop offset="0" stop-color="#1d5fb4"/>
        <stop offset="1" stop-color="#2f8ae0"/>
      </linearGradient>
    </defs>
    <path d="M0,238 C130,250 210,165 295,120 C345,98 425,88 506,84 L506,96 C425,100 350,110 302,132 C215,176 135,264 0,252 Z" fill="var(--swoosh-gray)"/>
    <path d="M0,266 C135,280 218,186 305,142 C355,118 428,110 506,106 L506,368 L0,368 Z" fill="url(#blueFill)"/>
  </svg>

  <div class="wordmark">
    <div class="wordmark__row">
      <span class="wordmark__mark"></span>
      <span class="wordmark__name">HALDEN</span>
    </div>
    <span class="wordmark__sub">CONTRACTING, INC.</span>
  </div>

  <div class="holder">
    <p class="holder__name">Daniel Whitford</p>
    <p class="holder__title">Managing Member</p>
  </div>

  <div class="contact">
    <p class="contact__address">2280 Meridian Way,<br>Sacramento, CA 95834</p>
    <p class="contact__line">(916) 555-0142
      <svg class="contact__icon" viewBox="0 0 10 10"><path d="M2 0h2l1 3-1.5 1a6 6 0 0 0 2.5 2.5L7 5l3 1v2a2 2 0 0 1-2 2A8 8 0 0 1 0 2a2 2 0 0 1 2-2z"/></svg></p>
    <p class="contact__line">(530) 555-0187
      <svg class="contact__icon" viewBox="0 0 10 10"><rect x="2" y="0" width="6" height="10" rx="1"/></svg></p>
    <p class="contact__line">daniel@haldenbuild.com
      <svg class="contact__icon" viewBox="0 0 10 10"><path d="M0 2h10v6H0z M0 2l5 3 5-3"/></svg></p>
    <p class="contact__line">www.haldenbuild.com
      <svg class="contact__icon" viewBox="0 0 10 10"><rect x="0" y="2" width="10" height="6"/></svg></p>
  </div>
</section>

<section class="card card--back">
  <div class="wordmark">
    <div class="wordmark__row">
      <span class="wordmark__mark"></span>
      <span class="wordmark__name">HALDEN</span>
    </div>
    <span class="wordmark__sub">CONTRACTING, INC.</span>
  </div>
</section>

</body>
</html>
```